Business Card Design Project

We are rebranding an existing automotive collision repair business. The business is called dent haven. I have attached logo but I'm not tied to that. I want to leave this wide open.

I want this card to say we are professional, competent, cutting edge. We are focused on customers and use a lot of the latest technology to make the customer experience different. We sign customers in on iPads. Paperwork I signed electronically and updates are sent via text, email, logging on a website or as they wish. I want this innovation and image to come through in our cards

Target Market(s)

60%. Women 40% men. Age 35-60

Industry/Entity Type

Automotive

Requirements
Must have
• The card must have name, title, phone,email, cell, web page

```html
<!DOCTYPE html>
<html lang="en">
<head>
<meta charset="utf-8">
<title>Dent Haven — Business Card</title>
<link rel="stylesheet" href="https://fonts.googleapis.com/css2?family=Arimo:wght@400;700&display=swap">
<style>
  :root {
    --backdrop: #e6e7e8;
    --brand-green: #67be47;
    --brand-green-dark: #4f9e35;
    --card-white: #ffffff;
    --pill-grey: #d4d5d7;
    --card-shadow: rgba(0, 0, 0, 0.38);
  }
  html, body {
    margin: 0;
    padding: 0;
    overflow: hidden;
  }
  body {
    width: 1200px;
    height: 800px;
    background: var(--backdrop);
    position: relative;
    font-family: "Arimo", Arial, sans-serif;
  }
  .card {
    position: absolute;
    height: 242px;
    filter: drop-shadow(3px 4px 3px var(--card-shadow));
    overflow: hidden;
  }

  /* Front side */
  .card--front {
    left: 102px;
    top: 268px;
    width: 428px;
    background: var(--brand-green);
    border-radius: 0 121px 121px 0;
  }
  .front__brand-pill {
    position: absolute;
    left: -2px;
    top: 77px;
    width: 233px;
    height: 84px;
    box-sizing: border-box;
    background: var(--pill-grey);
    border: 2px solid var(--card-white);
    border-radius: 0 43px 43px 0;
    display: flex;
    align-items: center;
    justify-content: center;
  }
  .brand-name {
    font-weight: 700;
    color: var(--brand-green);
    white-space: nowrap;
    letter-spacing: 0.2px;
  }
  .front__brand-pill .brand-name {
    font-size: 19px;
  }
  .front__web {
    position: absolute;
    left: 256px;
    top: 116px;
    font-size: 13px;
    color: var(--card-white);
  }

  /* Back side */
  .card--back {
    left: 678px;
    top: 270px;
    width: 422px;
    background: var(--card-white);
    border-radius: 121px 0 0 121px;
  }
  .back__brand {
    position: absolute;
    left: 30px;
    top: 107px;
    width: 130px;
    text-align: center;
  }
  .back__brand .brand-name {
    font-size: 19px;
  }
  .back__email {
    position: absolute;
    right: 14px;
    top: 42px;
    font-size: 13px;
    color: var(--brand-green);
  }
  .contact-label {
    font-weight: 700;
    color: var(--brand-green-dark);
    margin-right: 4px;
  }
  .back__name-band {
    position: absolute;
    left: 194px;
    top: 78px;
    width: 228px;
    height: 84px;
    background: var(--brand-green);
    border-radius: 42px 0 0 42px;
    color: var(--card-white);
    text-align: right;
    box-sizing: border-box;
    padding-right: 34px;
    padding-top: 22px;
  }
  .person-name {
    font-size: 18px;
    line-height: 22px;
  }
  .person-title {
    font-size: 14px;
    line-height: 20px;
  }
  .back__phones {
    position: absolute;
    left: 240px;
    top: 184px;
    font-size: 13px;
    line-height: 16px;
    color: var(--brand-green);
  }
</style>
</head>
<body>
  <section class="card card--front" aria-label="Card front">
    <div class="front__brand-pill">
      <span class="brand-name">Dent Haven</span>
    </div>
    <div class="front__web">www.denthaven.com</div>
  </section>

  <section class="card card--back" aria-label="Card back">
    <div class="back__brand"><span class="brand-name">Dent Haven</span></div>
    <div class="back__email"><span class="contact-label">E</span> hello@denthaven.com</div>
    <div class="back__name-band">
      <div class="person-name">Mara Ellison</div>
      <div class="person-title">Director</div>
    </div>
    <div class="back__phones">
      <div><span class="contact-label">T</span> +1 (800) 555-0142</div>
      <div><span class="contact-label">M</span> +1 (800) 555-0142</div>
    </div>
  </section>
</body>
</html>
```